brqnal new business card design project

we need a new business card design. you can view info about us @ brqnal-example.com. i have attached an example of our previous card with our previous name that we no longer use. We really liked the design, colors etc. look below to see more info about this project. it asks for a limited number of words. please see our website for more info about our compnay.

Target Market(s)

law enforcement

Contact Information for Business Card

i have uploaded an example of what we used before that we liked.

Font styles to use
Serif

```html
<!DOCTYPE html>
<html lang="en">
<head>
<meta charset="utf-8">
<title>BRQNAL Business Card</title>
<link rel="stylesheet" href="https://fonts.googleapis.com/css2?family=Ubuntu:wght@300;400&display=swap">
<style>
  :root {
    --page-bg: #d9d5d0;
    --card-bg: #eceeef;
    --ink: #1f2429;
    --ink-soft: #2c3238;
    --brand-blue: #1f6fa6;
    --band-dark: #1c2731;
  }
  * { margin: 0; padding: 0; box-sizing: border-box; }
  html, body {
    width: 1200px;
    height: 1054px;
    overflow: hidden;
    background: var(--page-bg);
  }
  .business-card {
    position: absolute;
    left: 100px;
    top: 225px;
    width: 1000px;
    height: 604px;
    background: var(--card-bg);
    box-shadow: 0 14px 40px rgba(0,0,0,0.18);
    overflow: hidden;
    font-family: "Ubuntu", sans-serif;
    color: var(--ink);
  }
  .brand-name {
    position: absolute;
    left: 58px;
    top: 58px;
    font-size: 98px;
    font-weight: 300;
    letter-spacing: 4px;
    line-height: 1;
    color: var(--ink);
  }
  .person-name {
    position: absolute;
    left: 54px;
    top: 228px;
    font-size: 40px;
    font-weight: 400;
    color: var(--brand-blue);
  }
  .person-title {
    position: absolute;
    left: 54px;
    top: 285px;
    font-size: 24px;
    font-weight: 300;
    color: var(--ink-soft);
  }
  .contact-list {
    position: absolute;
    left: 62px;
    top: 346px;
    list-style: none;
  }
  .contact-item {
    display: flex;
    align-items: center;
    height: 37.5px;
    font-size: 25px;
    font-weight: 300;
    color: var(--ink-soft);
  }
  .contact-icon {
    width: 22px;
    height: 22px;
    margin-right: 20px;
    fill: var(--brand-blue);
  }
  .address {
    position: absolute;
    left: 54px;
    top: 474px;
    font-size: 25px;
    font-weight: 300;
    color: var(--ink-soft);
  }
  .footer-band {
    position: absolute;
    left: 0;
    bottom: 0;
    width: 1000px;
    height: 46px;
  }
  .footer-web {
    position: absolute;
    right: 40px;
    top: 570px;
    font-size: 20px;
    line-height: 1;
    font-weight: 300;
    letter-spacing: 3px;
    white-space: nowrap;
    color: var(--ink);
  }
</style>
</head>
<body>
  <main class="business-card">
    <div class="brand-name">BRQNAL</div>

    <div class="person-name">Darren Holloway</div>
    <div class="person-title">Founder/Chief Executive Officer</div>

    <ul class="contact-list">
      <li class="contact-item">
        <svg class="contact-icon" viewBox="0 0 24 24" aria-hidden="true">
          <path d="M3 7c0-2 2-3 9-3s9 1 9 3v2h-5V7.5c-1-.4-2.5-.6-4-.6s-3 .2-4 .6V9H3z"/>
          <path d="M6 11h12l2 8H4z"/>
          <circle cx="12" cy="15" r="2" fill="#eceeef"/>
        </svg>
        866.555.0142
      </li>
      <li class="contact-item">
        <svg class="contact-icon" viewBox="0 0 24 24" aria-hidden="true">
          <path d="M2 5h20v14H2z"/>
          <path d="M2 5l10 8 10-8" fill="none" stroke="#eceeef" stroke-width="2"/>
        </svg>
        info@brqnal-example.com
      </li>
      <li class="contact-item">
        <svg class="contact-icon" viewBox="0 0 24 24" aria-hidden="true">
          <circle cx="12" cy="12" r="10"/>
          <g fill="none" stroke="#eceeef" stroke-width="1.4">
            <ellipse cx="12" cy="12" rx="4.5" ry="10"/>
            <path d="M2 12h20M4 7h16M4 17h16"/>
          </g>
        </svg>
        www.brqnal-example.com
      </li>
    </ul>

    <div class="address">4120 Meadowlark Lane Houston, TX 77041</div>

    <svg class="footer-band" viewBox="0 0 1000 46" aria-hidden="true">
      <polygon points="0,0 456,0 430,46 0,46" fill="var(--brand-blue)"/>
      <polygon points="479,0 616,0 597,46 460,46" fill="var(--band-dark)"/>
    </svg>
    <div class="footer-web">www.brqnal-example.com</div>
  </main>
</body>
</html>
```